Marketing Flyer for Ashford Hollow Storage Climate Control Units

We are looking for a professional looking Marketing Flyer to advertise for our Climate Control Self Storage Units. Incorporate photos and our LOGO into the marketing flyer. See our website: AshfordHollowstorage.example
Updates

Marketing Flyer for our Self Storage Climate Control Units at Ashford Hollow Storage in Waynesville, NC

Want more designers to have a chance to submit entries.

Target Market(s)

Self Storage Facility Renters

Industry/Entity Type

Self Storage Facility

Font styles to use
Other font styles liked:
• Montserrat Font is what was used for our LOGO and would like to maintain consistency of Font on the Flyer

Colors
0054AA
0677BA
7BADD7
CADEEF
E8F1F8

Requirements
Must have
• Need to have LOGO in the Flyer and photos of the Climate Control Units

```html
<!DOCTYPE html>
<html lang="en">
<head>
<meta charset="utf-8">
<title>Ashford Hollow Storage – Climate Control Flyer</title>
<link rel="stylesheet" href="https://fonts.googleapis.com/css2?family=Montserrat:wght@400;500;600;700;800;900&display=swap">
<style>
:root{
  --navy:#1b174f;
  --ink:#1a1a2e;
  --slate:#444448;
  --band-grey:#55565a;
  --paper:#ffffff;
  --backdrop:#e6e6e8;
  --sky-top:#7badd7;
  --sky-low:#cadeef;
  --brick:#9a5a40;
  --brick-dark:#6e3d2b;
  --pavement:#b9b9b9;
  --unit-blue:#0054aa;
}
*{box-sizing:border-box;margin:0;padding:0}
html,body{width:1200px;height:3008px;overflow:hidden}
body{background:var(--backdrop);font-family:"Montserrat",sans-serif;position:relative}
.flyer{position:absolute;width:870px;height:1125px;background:var(--paper);overflow:hidden;transform-origin:0 0;box-shadow:0 6px 22px rgba(0,0,0,.18)}
.flyer--first{left:95px;top:71px;transform:scale(1.167)}
.flyer--second{left:60px;top:1565px;transform:scale(1.22)}
.flyer__art{position:absolute;inset:0;width:870px;height:1125px}
.brand{position:absolute;left:46px;top:150px;width:340px;text-align:center;color:var(--navy);font-weight:600;letter-spacing:.5px}
.brand__name{font-size:31px;line-height:1.1}
.brand__sub{font-size:24px;letter-spacing:7px;margin-top:2px}
.headline{position:absolute;left:44px;top:250px;color:var(--ink);font-weight:900;font-size:76px;line-height:.86;letter-spacing:-1px}
.subhead{position:absolute;left:44px;top:387px;color:var(--slate);font-weight:800;font-size:33px;letter-spacing:.2px}
.call-bar{position:absolute;left:49px;top:449px;width:420px;height:82px;background:var(--navy);clip-path:polygon(0 0,100% 0,88% 100%,0 100%);color:#fff;padding:8px 0 0 14px}
.call-bar__name{font-size:25px;font-weight:500;letter-spacing:.2px}
.call-bar__phone{font-size:32px;font-weight:700;display:flex;align-items:center;gap:6px;margin-top:-2px}
.about__title{position:absolute;left:50px;top:548px;color:var(--slate);font-weight:800;font-size:34px}
.about__text{position:absolute;left:51px;top:596px;width:338px;font-size:10.6px;line-height:13.5px;color:#333}
.features-bar{position:absolute;left:49px;top:704px;width:372px;height:44px;background:var(--navy);clip-path:polygon(0 0,94% 0,100% 100%,0 100%);color:#fff;font-size:25px;font-weight:700;padding:7px 0 0 15px}
.feature-label{position:absolute;width:170px;margin-left:-85px;text-align:center;font-size:14px;font-weight:600;line-height:17px;color:var(--slate)}
.footer__address{position:absolute;left:43px;top:1060px;color:#fff;font-size:21px;font-weight:500;line-height:25px;display:flex;gap:10px}
.footer__web{position:absolute;left:484px;top:1075px;color:#fff;font-size:22px;font-weight:500;display:flex;align-items:center;gap:8px}
</style>
</head>
<body>

<svg width="0" height="0" style="position:absolute" aria-hidden="true">
  <defs>
    <linearGradient id="facade-tone" x1="0" y1="0" x2="0" y2="1">
      <stop offset="0" stop-color="var(--sky-top)"/>
      <stop offset=".3" stop-color="var(--sky-low)"/>
      <stop offset=".33" stop-color="var(--brick)"/>
      <stop offset=".65" stop-color="var(--brick-dark)"/>
      <stop offset=".72" stop-color="#8a8078"/>
      <stop offset="1" stop-color="var(--pavement)"/>
    </linearGradient>
    <linearGradient id="entry-tone" x1="0" y1="0" x2="0" y2="1">
      <stop offset="0" stop-color="var(--brick)"/>
      <stop offset=".7" stop-color="var(--brick-dark)"/>
      <stop offset="1" stop-color="#8f8f8f"/>
    </linearGradient>
    <linearGradient id="hall-tone" x1="0" y1="0" x2="1" y2="0">
      <stop offset="0" stop-color="#e8eaec"/>
      <stop offset=".45" stop-color="#c9ced4"/>
      <stop offset="1" stop-color="var(--unit-blue)"/>
    </linearGradient>
    <symbol id="feature-badge" viewBox="0 0 64 70">
      <polygon points="32,2 61,18 61,52 32,68 3,52 3,18" fill="#fff" stroke="#4a4a4e" stroke-width="3" stroke-linejoin="round"/>
      <polygon points="32,7 56,21 56,49 32,63 8,49 8,21" fill="#48484c" stroke-linejoin="round"/>
    </symbol>
  </defs>
</svg>

<section class="flyer flyer--first">
  <svg class="flyer__art" viewBox="0 0 870 1125" aria-hidden="false">
    <polygon points="228,0 870,0 870,380 455,125" fill="var(--navy)"/>
    <g stroke-linejoin="round">
      <polygon points="660,11 867,130 867,360 660,479 454,360 454,130" fill="url(#facade-tone)" stroke="var(--navy)" stroke-width="16" role="img" aria-label="Photo of the brick storage building exterior"/>
      <polygon points="660,11 867,130 867,360 660,479 454,360 454,130" fill="none" stroke="#fff" stroke-width="3"/>
      <polygon points="528,422 659,495 659,642 528,715 397,642 397,495" fill="url(#entry-tone)" stroke="var(--navy)" stroke-width="14" role="img" aria-label="Photo of the building entrance door"/>
      <polygon points="528,422 659,495 659,642 528,715 397,642 397,495" fill="none" stroke="#fff" stroke-width="3"/>
      <polygon points="790,426 915,498 915,633 790,705 664,633 664,498" fill="url(#hall-tone)" stroke="var(--navy)" stroke-width="14" role="img" aria-label="Photo of indoor hallway with blue roll-up unit doors"/>
      <polygon points="790,426 915,498 915,633 790,705 664,633 664,498" fill="none" stroke="#fff" stroke-width="3"/>
    </g>
    <g>
      <use href="#feature-badge" x="78" y="770" width="64" height="70"/>
      <use href="#feature-badge" x="215" y="770" width="64" height="70"/>
      <use href="#feature-badge" x="369" y="766" width="64" height="70"/>
      <use href="#feature-badge" x="536" y="770" width="64" height="70"/>
      <use href="#feature-badge" x="695" y="770" width="64" height="70"/>
      <use href="#feature-badge" x="78" y="902" width="64" height="70"/>
      <use href="#feature-badge" x="215" y="902" width="64" height="70"/>
      <use href="#feature-badge" x="369" y="902" width="64" height="70"/>
      <use href="#feature-badge" x="536" y="906" width="64" height="70"/>
      <use href="#feature-badge" x="695" y="904" width="64" height="70"/>
    </g>
    <g fill="#fff" stroke="#fff">
      <circle cx="110" cy="805" r="12" fill="none" stroke-width="3"/>
      <circle cx="247" cy="805" r="12" stroke="none"/>
      <rect x="391" y="790" width="20" height="20" rx="2" stroke="none"/>
      <rect x="557" y="793" width="22" height="24" rx="3" fill="none" stroke-width="3"/>
      <rect x="718" y="800" width="18" height="14" rx="2" stroke="none"/>
      <path d="M722 800v-5a5 5 0 0 1 10 0v5" fill="none" stroke-width="3"/>
      <path d="M104 947v-20M116 947v-20M100 931l4-5 4 5M112 931l4-5 4 5" fill="none" stroke-width="3"/>
      <circle cx="247" cy="930" r="7" stroke="none"/>
      <rect x="236" y="940" width="22" height="8" rx="2" stroke="none"/>
      <rect x="390" y="925" width="22" height="22" rx="2" fill="none" stroke-width="3"/>
      <path d="M552 950l10-8h18" fill="none" stroke-width="3"/>
      <circle cx="568" cy="932" r="5" stroke="none"/>
      <path d="M715 944l20-14 6 8-20 14z" stroke="none"/>
    </g>
    <polygon points="0,1054 430,1054 498,1125 0,1125" fill="var(--navy)"/>
    <polygon points="448,1062 870,1062 870,1125 510,1125" fill="var(--band-grey)"/>
  </svg>

  <div class="brand">
    <div class="brand__name">ASHFORD HOLLOW</div>
    <div class="brand__sub">STORAGE</div>
  </div>
  <h1 class="headline">CLIMATE<br>CONTROL</h1>
  <div class="subhead">SELF STORAGE UNITS</div>

  <div class="call-bar">
    <div class="call-bar__name">ASHFORD HOLLOW STORAGE</div>
    <div class="call-bar__phone">
      <svg width="16" height="16" viewBox="0 0 24 24" aria-hidden="true"><path fill="#fff" d="M6.6 10.8a15 15 0 0 0 6.6 6.6l2.2-2.2a1 1 0 0 1 1-.25 11.4 11.4 0 0 0 3.6.57 1 1 0 0 1 1 1V20a1 1 0 0 1-1 1A17 17 0 0 1 3 4a1 1 0 0 1 1-1h3.5a1 1 0 0 1 1 1c0 1.25.2 2.45.57 3.57a1 1 0 0 1-.25 1z"/></svg>
      555-555-0147
    </div>
  </div>

  <h2 class="about__title">ABOUT US</h2>
  <p class="about__text">We have proudly been serving the Fernbrook community for over 40 years! Recently renovated and now with brand new climate controlled units! Conveniently located on Orchard Ridge Road across from Fernbrook Community Park. We have every option for your storage needs with some of the best rates in town!</p>

  <div class="features-bar">FEATURES &amp; AMENITIES</div>

  <div class="feature-label" style="left:110px;top:846px">24/7<br>Access</div>
  <div class="feature-label" style="left:247px;top:846px">Climate<br>Controlled Units</div>
  <div class="feature-label" style="left:401px;top:842px">Ground<br>Floor Units</div>
  <div class="feature-label" style="left:568px;top:846px">Contactless Rental<br>and Payment</div>
  <div class="feature-label" style="left:727px;top:844px">Free<br>Locks</div>
  <div class="feature-label" style="left:110px;top:978px">Drive-Up<br>Units</div>
  <div class="feature-label" style="left:247px;top:978px">Phone<br>Support</div>
  <div class="feature-label" style="left:401px;top:978px">Covered Vehicle /<br>Boat / RV Parking</div>
  <div class="feature-label" style="left:568px;top:982px">Insurance<br>Services</div>
  <div class="feature-label" style="left:727px;top:980px">24/7 Security<br>Surveillance</div>

  <div class="footer__address">
    <svg width="14" height="18" viewBox="0 0 14 18" style="margin-top:6px" aria-hidden="true"><path d="M7 1a5 5 0 0 0-5 5c0 4 5 10 5 10s5-6 5-10a5 5 0 0 0-5-5z" fill="none" stroke="#fff" stroke-width="1.6"/><circle cx="7" cy="6" r="1.8" fill="#fff"/></svg>
    <span>42 Orchard Ridge Rd, Fernbrook,<br>ST 00000</span>
  </div>
  <div class="footer__web">
    <svg width="18" height="18" viewBox="0 0 20 20" aria-hidden="true"><g fill="none" stroke="#fff" stroke-width="1.5"><circle cx="10" cy="10" r="8"/><ellipse cx="10" cy="10" rx="3.5" ry="8"/><path d="M2 10h16M3.5 6h13M3.5 14h13"/></g></svg>
    AshfordHollowstorage.example
  </div>
</section>

<section class="flyer flyer--second">
  <svg class="flyer__art" viewBox="0 0 870 1125" aria-hidden="false">
    <polygon points="228,0 870,0 870,380 455,125" fill="var(--navy)"/>
    <g stroke-linejoin="round">
      <polygon points="660,11 867,130 867,360 660,479 454,360 454,130" fill="url(#facade-tone)" stroke="var(--navy)" stroke-width="16" role="img" aria-label="Photo of the brick storage building exterior"/>
      <polygon points="660,11 867,130 867,360 660,479 454,360 454,130" fill="none" stroke="#fff" stroke-width="3"/>
      <polygon points="528,422 659,495 659,642 528,715 397,642 397,495" fill="url(#entry-tone)" stroke="var(--navy)" stroke-width="14" role="img" aria-label="Photo of the building entrance door"/>
      <polygon points="528,422 659,495 659,642 528,715 397,642 397,495" fill="none" stroke="#fff" stroke-width="3"/>
      <polygon points="790,426 915,498 915,633 790,705 664,633 664,498" fill="url(#hall-tone)" stroke="var(--navy)" stroke-width="14" role="img" aria-label="Photo of indoor hallway with blue roll-up unit doors"/>
      <polygon points="790,426 915,498 915,633 790,705 664,633 664,498" fill="none" stroke="#fff" stroke-width="3"/>
    </g>
    <g>
      <use href="#feature-badge" x="78" y="770" width="64" height="70"/>
      <use href="#feature-badge" x="215" y="770" width="64" height="70"/>
      <use href="#feature-badge" x="369" y="766" width="64" height="70"/>
      <use href="#feature-badge" x="536" y="770" width="64" height="70"/>
      <use href="#feature-badge" x="695" y="770" width="64" height="70"/>
      <use href="#feature-badge" x="78" y="902" width="64" height="70"/>
      <use href="#feature-badge" x="215" y="902" width="64" height="70"/>
      <use href="#feature-badge" x="369" y="902" width="64" height="70"/>
      <use href="#feature-badge" x="536" y="906" width="64" height="70"/>
      <use href="#feature-badge" x="695" y="904" width="64" height="70"/>
    </g>
    <g fill="#fff" stroke="#fff">
      <circle cx="110" cy="805" r="12" fill="none" stroke-width="3"/>
      <circle cx="247" cy="805" r="12" stroke="none"/>
      <rect x="391" y="790" width="20" height="20" rx="2" stroke="none"/>
      <rect x="557" y="793" width="22" height="24" rx="3" fill="none" stroke-width="3"/>
      <rect x="718" y="800" width="18" height="14" rx="2" stroke="none"/>
      <path d="M722 800v-5a5 5 0 0 1 10 0v5" fill="none" stroke-width="3"/>
      <path d="M104 947v-20M116 947v-20M100 931l4-5 4 5M112 931l4-5 4 5" fill="none" stroke-width="3"/>
      <circle cx="247" cy="930" r="7" stroke="none"/>
      <rect x="236" y="940" width="22" height="8" rx="2" stroke="none"/>
      <rect x="390" y="925" width="22" height="22" rx="2" fill="none" stroke-width="3"/>
      <path d="M552 950l10-8h18" fill="none" stroke-width="3"/>
      <circle cx="568" cy="932" r="5" stroke="none"/>
      <path d="M715 944l20-14 6 8-20 14z" stroke="none"/>
    </g>
    <polygon points="0,1054 430,1054 498,1125 0,1125" fill="var(--navy)"/>
    <polygon points="448,1062 870,1062 870,1125 510,1125" fill="var(--band-grey)"/>
  </svg>

  <div class="brand">
    <div class="brand__name">ASHFORD HOLLOW</div>
    <div class="brand__sub">STORAGE</div>
  </div>
  <h1 class="headline">CLIMATE<br>CONTROL</h1>
  <div class="subhead">SELF STORAGE UNITS</div>

  <div class="call-bar">
    <div class="call-bar__name">ASHFORD HOLLOW STORAGE</div>
    <div class="call-bar__phone">
      <svg width="16" height="16" viewBox="0 0 24 24" aria-hidden="true"><path fill="#fff" d="M6.6 10.8a15 15 0 0 0 6.6 6.6l2.2-2.2a1 1 0 0 1 1-.25 11.4 11.4 0 0 0 3.6.57 1 1 0 0 1 1 1V20a1 1 0 0 1-1 1A17 17 0 0 1 3 4a1 1 0 0 1 1-1h3.5a1 1 0 0 1 1 1c0 1.25.2 2.45.57 3.57a1 1 0 0 1-.25 1z"/></svg>
      555-555-0147
    </div>
  </div>

  <h2 class="about__title">ABOUT US</h2>
  <p class="about__text">We have proudly been serving the Fernbrook community for over 40 years! Recently renovated and now with brand new climate controlled units! Conveniently located on Orchard Ridge Road across from Fernbrook Community Park. We have every option for your storage needs with some of the best rates in town!</p>

  <div class="features-bar">FEATURES &amp; AMENITIES</div>

  <div class="feature-label" style="left:110px;top:846px">24/7<br>Access</div>
  <div class="feature-label" style="left:247px;top:846px">Climate<br>Controlled Units</div>
  <div class="feature-label" style="left:401px;top:842px">Ground<br>Floor Units</div>
  <div class="feature-label" style="left:568px;top:846px">Contactless Rental<br>and Payment</div>
  <div class="feature-label" style="left:727px;top:844px">Free<br>Locks</div>
  <div class="feature-label" style="left:110px;top:978px">Drive-Up<br>Units</div>
  <div class="feature-label" style="left:247px;top:978px">Phone<br>Support</div>
  <div class="feature-label" style="left:401px;top:978px">Covered Vehicle /<br>Boat / RV Parking</div>
  <div class="feature-label" style="left:568px;top:982px">Insurance<br>Services</div>
  <div class="feature-label" style="left:727px;top:980px">24/7 Security<br>Surveillance</div>

  <div class="footer__address">
    <svg width="14" height="18" viewBox="0 0 14 18" style="margin-top:6px" aria-hidden="true"><path d="M7 1a5 5 0 0 0-5 5c0 4 5 10 5 10s5-6 5-10a5 5 0 0 0-5-5z" fill="none" stroke="#fff" stroke-width="1.6"/><circle cx="7" cy="6" r="1.8" fill="#fff"/></svg>
    <span>42 Orchard Ridge Rd, Fernbrook,<br>ST 00000</span>
  </div>
  <div class="footer__web">
    <svg width="18" height="18" viewBox="0 0 20 20" aria-hidden="true"><g fill="none" stroke="#fff" stroke-width="1.5"><circle cx="10" cy="10" r="8"/><ellipse cx="10" cy="10" rx="3.5" ry="8"/><path d="M2 10h16M3.5 6h13M3.5 14h13"/></g></svg>
    AshfordHollowstorage.example
  </div>
</section>

</body>
</html>
```